Plotvista Caribbean

We need a vibrant, user friendly and exciting website for our land search company called "plotVista" This application will help individuals locate and or list lots for sale within the Caribbean. We will offer a small cash back incentive to buyers that purchase land from our site, and we will charge a 1%-2% success fee to our sellers once a successful transaction is made. We would like to become a match making site, matching buyers and sellers on our platform. We will also include a service directory and marketing advertisement spot for other service providers for a fee. We would like to see a webdesign incorporating Caribbean colors (blue, green and yellow) with very modern clean lines, very picturesque and easy to use.

Industry/Entity Type

Real Estate

Coding

Coded - Design and coding required

Number of Pages Required

5+ page

Font styles to use
Sans Serif

Colors
ffffff
85acd3
b768aa
dbdbdb

Requirements
Nice to have
• Scenic photos of the ocean and beautiful landscape

```html
<!DOCTYPE html>
<html lang="en">
<head>
<meta charset="utf-8">
<title>plotVista</title>
<link rel="stylesheet" href="https://fonts.googleapis.com/css2?family=Jost:wght@400;500&family=Arimo:wght@400&display=swap">
<style>
:root{
  --white:#ffffff;
  --blue:#85acd3;
  --purple:#b768aa;
  --grey:#dbdbdb;
  --ink:#3a3a3a;
  --muted:#666666;
  --navtext:#8a8a8a;
}
*{box-sizing:border-box;margin:0;padding:0}
html,body{width:1200px;height:3158px;overflow:hidden;background:var(--white)}
body{position:relative;font-family:"Jost",sans-serif;color:var(--ink)}
.abs{position:absolute}
.body-copy{font-family:"Arimo",sans-serif;font-size:14px;line-height:23px;color:var(--muted)}

/* header */
.site-header{left:0;top:0;width:1200px;height:101px;background:var(--white)}
.brand{left:112px;top:20px;font-size:44px;font-weight:400;color:var(--blue);letter-spacing:.5px}
.main-nav{right:118px;top:38px;display:flex;gap:31px;font-size:18px;color:var(--navtext)}
.main-nav .active{color:var(--purple)}

/* hero */
.hero{left:0;top:101px;width:1200px;height:564px;
  background:linear-gradient(100deg,#2f8fb8 0%,#4aa7c7 25%,#d8cbb0 42%,#7a8e5c 55%,#3e6a33 75%,#2e5527 100%)}
.hero-title{left:0;width:1200px;top:276px;text-align:center;color:var(--white);font-size:50px;line-height:60px}
.hero-sub{left:0;width:1200px;top:334px;text-align:center;color:var(--white);font-size:35px;line-height:44px}
.btn{display:flex;align-items:center;justify-content:center;font-size:15px;letter-spacing:.5px;text-transform:uppercase}
.btn-buy{left:432px;top:406px;width:155px;height:42px;background:var(--blue);color:var(--white)}
.btn-sell{left:596px;top:406px;width:156px;height:42px;border:2px solid var(--white);color:var(--white)}
.slider-dots{left:544px;top:623px;display:flex;gap:8px}
.slider-dots span{width:16px;height:16px;border-radius:50%;background:var(--white)}
.slider-dots span.current{background:transparent;border:2px solid var(--white)}

/* welcome */
.welcome-title{left:112px;top:738px;font-size:38px;color:#222}
.welcome-copy{left:116px;top:804px;width:510px}
.welcome-copy p+p{margin-top:12px}
.btn-outline-purple{left:116px;top:994px;width:162px;height:44px;border:2px solid var(--purple);color:var(--purple)}
.audience-box{left:669px;width:419px;color:var(--white);padding:20px 36px 0 36px}
.audience-box h3{font-size:30px;font-weight:400;line-height:36px}
.audience-box p{font-family:"Arimo",sans-serif;font-size:12px;line-height:18px;margin-top:4px}
.audience-box .more{font-size:16px;margin-top:14px;display:block}
.box-buyers{top:737px;height:156px;background:var(--purple);border:3px solid #e9d3e5}
.box-sellers{top:901px;height:154px;background:var(--blue)}

/* locate */
.locate{left:0;top:1122px;width:1200px;height:480px;
  background:linear-gradient(110deg,#9fb4c8 0%,#6f9a4d 22%,#5a6a4a 42%,#6f8ea8 60%,#2e5a86 100%)}
.locate-title{left:684px;top:1228px;font-size:36px;color:var(--white)}
.locate-copy{left:684px;top:1290px;width:420px;font-family:"Arimo",sans-serif;font-size:15px;line-height:22px;color:var(--white)}
.locate-copy p+p{margin-top:14px}
.btn-outline-white{left:684px;top:1453px;width:158px;height:44px;border:2px solid var(--white);color:var(--white)}

/* featured */
.section-title{left:0;width:1200px;text-align:center;font-size:33px}
.featured-title{top:1648px;color:var(--purple)}
.featured-title .rule{display:inline-block;width:42px;height:2px;background:var(--purple);vertical-align:middle;margin:0 12px}
.land-card{top:1718px;width:320px;height:368px;border:2px solid var(--grey);background:var(--white)}
.land-card .photo{width:100%;height:206px}
.land-card h4{text-align:center;font-size:20px;font-weight:400;color:var(--blue);margin-top:12px}
.land-card p{text-align:center;font-family:"Arimo",sans-serif;font-size:13px;line-height:19px;color:var(--muted);margin-top:6px;padding:0 20px}
.land-card .price{position:absolute;left:48px;bottom:26px;font-size:28px;color:var(--purple)}
.land-card .info{position:absolute;right:40px;bottom:26px;width:112px;height:34px;background:var(--blue);color:var(--white);font-size:12px}
.card-dots{left:554px;top:2108px;display:flex;gap:8px}
.card-dots span{width:32px;height:5px;background:#777}
.card-dots span.current{background:var(--blue)}

/* why */
.why{left:0;top:2162px;width:1200px;height:421px;
  background:linear-gradient(180deg,#f2f7fb 0%,#cfe1f0 40%,#9fc4e3 62%,#2f6ea8 70%,#1c4f84 100%)}
.why-title{top:2226px;color:#333}
.why-icon{width:116px;height:114px;border-radius:14px;background:var(--blue);display:flex;align-items:center;justify-content:center}
.why-text{font-size:22px;line-height:31px;color:#1f5b8f;width:330px}

/* testimonial */
.testi-title{top:2632px;color:#333}
.client-photo{left:196px;top:2697px;width:180px;height:180px;border-radius:50%;background:linear-gradient(160deg,#9db08a,#c59a7c 60%,#6b4e3a)}
.quote-text{left:420px;top:2718px;width:590px;font-family:"Arimo",sans-serif;font-size:15px;line-height:29px;color:var(--muted)}
.quote-mark{font-family:"Jost",sans-serif;font-size:50px;color:var(--purple);line-height:1}
.author{left:408px;top:2824px;font-family:"Arimo",sans-serif;font-size:16px;color:#333}

/* footer */
.site-footer{left:0;top:2974px;width:1200px;height:184px;background:var(--purple);color:var(--white)}
.footer-nav{left:0;width:1200px;top:3010px;display:flex;justify-content:center;gap:27px;font-size:18px;color:var(--white)}
.copyright{left:0;width:1200px;top:3042px;text-align:center;font-family:"Arimo",sans-serif;font-size:14px;color:#f0dcec}
.social{left:505px;top:3087px;display:flex;gap:9px}
.social span{width:42px;height:42px;border-radius:50%;border:2px solid var(--white)}
</style>
</head>
<body>

<header class="abs site-header">
  <div class="abs brand">plotVista</div>
  <nav class="abs main-nav">
    <span class="active">Home</span><span>About Us</span><span>Services</span><span>Land</span><span>Buyer</span><span>Seller</span><span>Why Us</span><span>Contact</span>
  </nav>
</header>

<section class="abs hero" role="img" aria-label="Aerial view of a turquoise coastline with a beach and a road through green forest"></section>
<h1 class="abs hero-title" style="font-weight:400">Class aptent sociosqu litora</h1>
<div class="abs hero-sub">Aorquent per conubia inceptos</div>
<div class="abs btn btn-buy">Buy Now</div>
<div class="abs btn btn-sell">Sell Now</div>
<div class="abs slider-dots"><span class="current"></span><span></span><span></span><span></span></div>

<h2 class="abs welcome-title" style="font-weight:400">Welcome to plotVista</h2>
<div class="abs welcome-copy body-copy">
  <p>Praesent sit amet est in dictum dolor eu dictum porttitor enim felis viverra mi eget luctus massa purus quis odio Etiam nulla massa pharetra facilisis volutpat in imperdiet sit amet sem Aliquam nec erat gue augue et malesuada iaculis ipsum du aliquet feli</p>
  <p>vestibulum gravida Praesent elementum elit at tellus Curabitur metus ipsum luctus eu malesuada ut tincidunt sed diam</p>
</div>
<div class="abs btn btn-outline-purple">Read More</div>

<div class="abs audience-box box-buyers">
  <h3>For Buyers</h3>
  <p>felis viverra mi eget luctus massa purus quis odio Etiam nulla massa pharetra facilisis volutpat</p>
  <span class="more">Click here ›</span>
</div>
<div class="abs audience-box box-sellers">
  <h3>For Sellers</h3>
  <p>felis viverra mi eget luctus massa purus quis odio Etiam nulla massa pharetra facilisis volutpat</p>
  <span class="more">Click here ›</span>
</div>

<section class="abs locate" role="img" aria-label="Green mountain cliffs under a misty blue sky"></section>
<h2 class="abs locate-title" style="font-weight:400">Locate Land to Buy</h2>
<div class="abs locate-copy">
  <p>Pellentesque faucibus Ut accumsan ultricies elit Maec enas at justo id velit placerat moles</p>
  <p>tie Donec dictum lectus non odio Cras a ante vitae enim iaculis aliquam Mauris nunc quam venenatis nec euismod sit amet egestas placerat est</p>
</div>
<div class="abs btn btn-outline-white">Read More</div>

<h2 class="abs section-title featured-title" style="font-weight:400"><span class="rule"></span>Featured Lands<span class="rule"></span></h2>

<article class="abs land-card" style="left:107px">
  <div class="photo" role="img" aria-label="Sandy coastal land by the sea" style="background:linear-gradient(180deg,#9cc3e0 0%,#d9c7a8 45%,#c7814e 75%,#e2d3bf 100%)"></div>
  <h4>Land Tittle here</h4>
  <p>Maecenas aliquet velit vel turpis Mauris neque metus malesuada nec ultrici</p>
  <span class="price">$12,999</span><span class="info btn">More Info</span>
</article>
<article class="abs land-card" style="left:438px">
  <div class="photo" role="img" aria-label="Rolling green hills with farmland" style="background:linear-gradient(180deg,#c7d9e8 0%,#8fae6a 35%,#5f8a3a 70%,#7a9a45 100%)"></div>
  <h4>Land Tittle here</h4>
  <p>Maecenas aliquet velit vel turpis Mauris neque metus malesuada nec ultrici</p>
  <span class="price">$12,999</span><span class="info btn">More Info</span>
</article>
<article class="abs land-card" style="left:774px">
  <div class="photo" role="img" aria-label="Terraced green rice fields" style="background:linear-gradient(160deg,#5d8a2e 0%,#8cbf3f 50%,#4f7d25 100%)"></div>
  <h4>Land Tittle here</h4>
  <p>Maecenas aliquet velit vel turpis Mauris neque metus malesuada nec ultrici</p>
  <span class="price">$12,999</span><span class="info btn">More Info</span>
</article>
<div class="abs card-dots"><span></span><span class="current"></span><span></span></div>

<section class="abs why" role="img" aria-label="Calm blue sea under a bright sky"></section>
<h2 class="abs section-title why-title" style="font-weight:400">Why Choose Us</h2>
<div class="abs why-icon" style="left:120px;top:2330px">
  <svg width="80" height="80" viewBox="0 0 80 80" fill="none" stroke="#fff" stroke-width="3">
    <circle cx="34" cy="18" r="10"/><circle cx="52" cy="32" r="8"/>
    <path d="M8 60 L22 50 Q30 46 40 50 L52 52 Q56 54 52 58 L36 58"/>
    <path d="M20 70 L34 66 L60 62 Q72 56 70 52 L54 56"/>
  </svg>
</div>
<p class="abs why-text" style="left:257px;top:2330px">We will offer a small cash back incentive to buyers that purchase land from our site</p>
<div class="abs why-icon" style="left:608px;top:2330px">
  <svg width="70" height="70" viewBox="0 0 70 70" fill="none" stroke="#fff" stroke-width="6">
    <circle cx="20" cy="20" r="8"/><circle cx="50" cy="50" r="8"/><path d="M54 14 L16 56"/>
  </svg>
</div>
<p class="abs why-text" style="left:751px;top:2330px">We will charge a 1%-2% success fee to our sellers once a successful transaction is made</p>

<h2 class="abs section-title testi-title" style="font-weight:400">What Our Client Says</h2>
<svg class="abs" style="left:108px;top:2763px" width="22" height="40" viewBox="0 0 22 40" fill="none" stroke="#bbb" stroke-width="3"><path d="M19 3 L4 20 L19 37"/></svg>
<svg class="abs" style="left:1066px;top:2763px" width="22" height="40" viewBox="0 0 22 40" fill="none" stroke="#bbb" stroke-width="3"><path d="M3 3 L18 20 L3 37"/></svg>
<div class="abs client-photo" role="img" aria-label="Portrait photo of the client"></div>
<span class="abs quote-mark" style="left:384px;top:2700px">“</span>
<p class="abs quote-text">Proesent elementum elit at tellus nec ultricies sit amet porttitor mattis enim In massa libero interdum nec interdum vel blandit sed nulla In ullamcorper est eget tempor cursus neque mi consectetuer mi a ultricies massa est</p>
<span class="abs quote-mark" style="left:858px;top:2806px">”</span>
<div class="abs author">By Author Name</div>

<footer class="abs site-footer"></footer>
<nav class="abs footer-nav">
  <span>Home</span><span>About Us</span><span>Services</span><span>Land</span><span>Buyer</span><span>Seller</span><span>Why Us</span><span>Contact</span>
</nav>
<div class="abs copyright">© 2017 Company Name  All right reserved</div>
<div class="abs social"><span></span><span></span><span></span><span></span></div>

</body>
</html>
```